Pinecrest Real Estate A5 Flyer

A5 Flyer for print distribution.

Front (include attached photo and branding):
Pinecrest are a new face in the Dunmore & Kelvinhurst real estate market. The Pinecrest team are both Dunmore ‘locals’ and are genuinely and sincerely committed to this community. They put people first and pursue exceptional outcomes for their clients. This is the founding vision of Pinecrest.

Values:
Outstanding Customer Service
Timely Communication
Integrity Always
People First
Exceptional Negotiation

If you’re thinking of selling, interested in a free market appraisal, or simply want to find out more about the Pinecrest team, please reach out to Trevor or Owen for a chat. We’d love to shout you a coffee at The Marigold Coffee + Kitchen.

Pinecrest Real Estate
E: hello@pinecrestrealestate-example.com.au
W: pinecrestrealestate-example.com.au

Back (half the page about Trevor, other half the page about Owen). Please include headshots (Owen is the younger one):

Owen Pritchard (Property Consultant):

Owen has an in-depth understanding of all things property & finance related. With a degree in property & finance, diploma in finance & mortgage broking, certificate IV in real estate practice, project management roles in residential property development, plus years of small business experience as co-founder/co-owner of The Marigold Coffee + Kitchen, his experience in managing competing demands and complex scenarios runs far and wide.

Owen also has experience in corporate negotiations which is proving to be a very beneficial skill set. Owen is deeply committed to people and pursuing exceptional outcomes for his clients. He has built a reputation as a man of his word who is genuine and sincere and willing to go above and beyond for his clients.

owen@pinecrestrealestate-example.com.au
0400 118 204

Trevor Bungey (Director / Licensee):

Trevor has worked in various roles inclusive of being a Real Estate Agent, Bank Manager, Financial Counsellor, Mortgage Broker, and previously a Commercial Pilot. He spent eight years in remote Western Australia, where he worked for an international mining company creating strategies to help support the well-being of employees. Trevor’s focus in life has always been to help people. To him, it is always about the relationship. Trevor gets enormous satisfaction from seeing individuals, families, and businesses thrive financially. He has become a skilled negotiator with extensive experience working for a number of corporations and private firms.
 
What differentiates Trevor is his compassion and commitment to people. He works hard to be an excellent communicator with the aim of achieving great results. He  has extensive sales experience with incredible ability to push the boundaries, think outside the box and meet or surpass expectations. This is why his clients keep coming back and continue to refer well into the future. 

trevor@pinecrestrealestate-example.com.au
0400 362 917

Target Market(s)

House Sellers / House Buyers

Industry/Entity Type

Real Estate

Colors
0054AA
0677BA
7BADD7
CADEEF
E8F1F8

Requirements
Must have
• Branding / logo, river photo, head shots, company details etc
Nice to have
• Design as per attached branding guide

```html
<!DOCTYPE html>
<html lang="en">
<head>
<meta charset="utf-8">
<title>Pinecrest Real Estate – A5 Flyer</title>
<link href="https://fonts.googleapis.com/css2?family=Heebo:wght@400;500;700;800&display=swap" rel="stylesheet">
<style>
:root{
  --navy:#10223a;
  --ink:#1b2331;
  --paper:#ffffff;
  --backdrop:#b3b3b3;
  --hero-top:#c9d6e2;
  --hero-bottom:#4a6d8f;
}
*{margin:0;padding:0;box-sizing:border-box}
html,body{width:1200px;height:904px;overflow:hidden;background:var(--backdrop)}
body{font-family:"Heebo",Arial,sans-serif;color:var(--ink)}
.stage{position:relative;width:1200px;height:904px}

/* ---------- front ---------- */
.front{position:absolute;left:58px;top:79px;width:526px;height:746px;background:var(--paper);overflow:hidden}
.brand{position:absolute;top:29px;left:0;width:100%;display:flex;justify-content:center;align-items:center;gap:11px}
.brand-dot{width:40px;height:40px;border-radius:50%;background:var(--navy)}
.brand-name{font-size:25px;font-weight:500;letter-spacing:7px;color:var(--navy)}
.hero{position:absolute;left:0;top:84px;width:100%;height:244px;
  background:linear-gradient(180deg,var(--hero-top) 0%,var(--hero-bottom) 100%)}
.headline-band{position:absolute;left:0;top:328px;width:100%;height:79px;background:var(--navy);
  display:flex;align-items:center;justify-content:center;text-align:center}
.headline{color:#fff;font-weight:800;font-size:25.5px;line-height:30px;letter-spacing:-.2px}
.intro{position:absolute;left:0;top:415px;width:100%;text-align:center;font-size:13.3px;font-weight:500;line-height:16.5px}
.values-title{position:absolute;left:0;top:484px;width:100%;text-align:center;font-size:16px;font-weight:800}
.values-tree{position:absolute;left:0;top:500px}
.value-label{position:absolute;top:594px;width:110px;margin-left:-55px;text-align:center;font-size:13px;font-weight:500;line-height:16.3px}
.cta{position:absolute;left:0;top:648px;width:100%;text-align:center;font-size:13px;font-weight:500;line-height:16px}
.front-footer{position:absolute;left:0;top:709px;width:100%;height:37px;background:var(--navy);color:#fff;
  display:flex;align-items:center;justify-content:center;gap:9px;font-size:9.6px;font-weight:500;white-space:nowrap}
.front-footer .company{font-weight:700;font-size:10.4px}
.front-footer .item{display:flex;align-items:center;gap:4px}

/* ---------- back ---------- */
.back{position:absolute;left:617px;top:79px;width:526px;height:746px;background:var(--navy)}
.back-sheet{position:absolute;left:12px;top:12px;width:502px;height:722px;background:var(--paper);overflow:hidden}
.profile-photo{position:absolute;width:131px;
  background:linear-gradient(180deg,#f4f5f7 0%,#e6e9ee 30%,#5c6f8d 62%,#26385a 100%);border-radius:60px 60px 0 0}
.profile-name{position:absolute;left:21px;font-size:17.5px;white-space:nowrap;color:var(--navy)}
.profile-name strong{font-weight:800;letter-spacing:-.3px}
.profile-name span{font-weight:500}
.copy{position:absolute;left:22px;font-size:12.6px;letter-spacing:.15px;line-height:15.8px;white-space:nowrap;z-index:2}
.copy span{display:block}
.contact-bar{position:absolute;right:0;width:264px;height:51px;background:var(--navy);
  clip-path:polygon(25px 0,100% 0,100% 100%,0 100%);color:#fff;z-index:1}
.contact-row{position:absolute;right:27px;display:flex;align-items:center;gap:7px;font-weight:500;white-space:nowrap}
.contact-row .phone{font-size:11.8px}
.contact-row .email{font-size:10px}
.icon-dot{width:14px;height:14px;border-radius:50%;background:#dfe3ea;display:flex;align-items:center;justify-content:center}
</style>
</head>
<body>
<div class="stage">

  <!-- FRONT -->
  <section class="front">
    <div class="brand">
      <div class="brand-dot"></div>
      <div class="brand-name">PINECREST</div>
    </div>
    <div class="hero" role="img" aria-label="Aerial photo of the river foreshore with waterside homes, moored boats and the city skyline beyond"></div>
    <div class="headline-band">
      <h1 class="headline">Pinecrest are a new face in the<br>Dunmore &amp; Kelvinhurst real estate market.</h1>
    </div>
    <p class="intro">The Pinecrest team are both Dunmore ‘locals’ and are genuinely and sincerely<br>committed to this community. They put people first and pursue exceptional<br>outcomes for their clients. This is the founding vision of Pinecrest.</p>
    <h2 class="values-title">VALUES:</h2>
    <svg class="values-tree" width="526" height="92" viewBox="0 0 526 92" fill="none">
      <g stroke="#10223a" stroke-width="2.2">
        <path d="M79 37 V12 H463 V37"/>
        <path d="M189 12 V37 M280 12 V37 M372 12 V37"/>
      </g>
      <g fill="#10223a">
        <circle cx="79" cy="62" r="25.5"/><circle cx="189" cy="62" r="25.5"/><circle cx="280" cy="62" r="25.5"/><circle cx="372" cy="62" r="25.5"/><circle cx="463" cy="62" r="25.5"/>
      </g>
      <g stroke="#fff" stroke-width="1.2">
        <circle cx="79" cy="62" r="22.5"/><circle cx="189" cy="62" r="22.5"/><circle cx="280" cy="62" r="22.5"/><circle cx="372" cy="62" r="22.5"/><circle cx="463" cy="62" r="22.5"/>
      </g>
      <g stroke="#fff" stroke-width="1.2" stroke-linecap="round" stroke-linejoin="round">
        <circle cx="77" cy="61" r="5"/>
        <path d="M68 63 v-3 a9 9 0 0 1 18 0 v3"/>
        <rect x="66" y="61" width="3.5" height="6" rx="1"/>
        <path d="M86 66 q0 5 -6 5"/>
        <path d="M70 74 q7 -6 14 0"/>
        <rect x="85" y="50" width="8" height="6" rx="1"/>
        <path d="M178 60 h13 a3 3 0 0 1 3 3 v5 a3 3 0 0 1 -3 3 h-8 l-4 3 v-3 h-1 a3 3 0 0 1 -3 -3 v-5 a3 3 0 0 1 3 -3 z"/>
        <path d="M186 57 v-3 a3 3 0 0 1 3 -3 h11 a3 3 0 0 1 3 3 v5 a3 3 0 0 1 -3 3 v3 l-4 -3"/>
        <path d="M181 65.5 h1 M185 65.5 h1 M189 65.5 h1"/>
        <path d="M266 56 l6 -2 l7 4 l7 -4 l6 2 v10 l-7 6 l-6 -4 l-7 4 l-6 -6 z"/>
        <path d="M272 62 l5 5 M276 60 l5 5 M280 58 l5 5"/>
        <circle cx="372" cy="51" r="3"/>
        <path d="M367 58 h10 v10 h-2 v8 h-6 v-8 h-2 z"/>
        <path d="M362 77 h20"/>
        <path d="M455 48 h12 l4 4 v15 h-16 z"/>
        <path d="M459 58 l3 3 l5 -6"/>
        <path d="M452 72 l5 -3 l5 3 l5 -3 l5 3 l-5 4 h-10 z"/>
      </g>
    </svg>
    <div class="value-label" style="left:79px">Outstanding<br>Customer Service</div>
    <div class="value-label" style="left:189px">Timely<br>Communication</div>
    <div class="value-label" style="left:280px">Integrity<br>Always</div>
    <div class="value-label" style="left:372px">People<br>First</div>
    <div class="value-label" style="left:463px">Exceptional<br>Negotiation</div>
    <p class="cta">If you’re thinking of selling, interested in a free market appraisal, or simply want<br>to find out more about the Pinecrest team, please reach out to Trevor or Owen<br>for a chat. We’d love to shout you a coffee at The Marigold Coffee + Kitchen.</p>
    <footer class="front-footer">
      <span class="company">Pinecrest Real Estate</span>
      <span class="item">
        <svg width="12" height="12" viewBox="0 0 12 12" fill="none" stroke="#fff" stroke-width="1"><circle cx="6" cy="6" r="5.4"/><rect x="3" y="4" width="6" height="4.2"/><path d="M3 4 l3 2.3 l3 -2.3"/></svg>
        hello@pinecrestrealestate-example.com.au
      </span>
      <span class="item">
        <svg width="12" height="12" viewBox="0 0 12 12" fill="none" stroke="#fff" stroke-width="1"><circle cx="6" cy="6" r="5.4"/><ellipse cx="6" cy="6" rx="2.4" ry="5.4"/><path d="M0.8 6 h10.4 M1.6 3.4 h8.8 M1.6 8.6 h8.8"/></svg>
        pinecrestrealestate-example.com.au
      </span>
    </footer>
  </section>

  <!-- BACK -->
  <section class="back">
    <div class="back-sheet">
      <h2 class="profile-name" style="top:17px"><strong>OWEN PRITCHARD</strong> <span>(Property Consultant):</span></h2>
      <div class="profile-photo" style="left:371px;top:15px;height:242px" role="img" aria-label="Headshot of Owen Pritchard in a navy suit on a white background"></div>
      <div class="copy" style="top:42px">
        <span>Owen has an in-depth understanding of all things property &amp;</span>
        <span>finance related. With a degree in property &amp; finance, diploma</span>
        <span>in finance and mortgage broking, certificate IV in real estate</span>
        <span>practice, project management roles in residential property</span>
        <span>development, plus years of small business experience as</span>
        <span>co-founder/co-owner of The Marigold Coffee + Kitchen, his</span>
        <span>experience in managing competing demands and complex</span>
        <span>scenarios runs far and wide.</span>
      </div>
      <div class="copy" style="top:184px">
        <span>Owen also has experience in corporate negotiations</span>
        <span>which is proving to be a very beneficial skill set.</span>
        <span>Owen is deeply committed to people &amp; pursuing</span>
        <span>exceptional outcomes for his clients. He has built</span>
        <span>a reputation as a man of his word who is</span>
        <span>genuine and sincere and willing to go</span>
        <span>above and beyond for his clients.</span>
      </div>
      <div class="contact-bar" style="top:257px">
        <div class="contact-row" style="top:8px"><span class="phone">0400 118 204</span>
          <span class="icon-dot"><svg width="8" height="8" viewBox="0 0 8 8"><path d="M1.5 1 l1.4 -.2 l.8 1.7 l-.9 .7 q.8 1.7 2 2 l.7 -.9 l1.7 .8 l-.2 1.4 q-4.5 .3 -5.5 -5.5z" fill="#10223a"/></svg></span></div>
        <div class="contact-row" style="top:27px"><span class="email">owen@pinecrestrealestate-example.com.au</span>
          <span class="icon-dot"><svg width="8" height="8" viewBox="0 0 8 8" fill="none" stroke="#10223a" stroke-width="1"><rect x=".8" y="1.8" width="6.4" height="4.6"/><path d="M.8 1.8 l3.2 2.5 l3.2 -2.5"/></svg></span></div>
      </div>

      <h2 class="profile-name" style="top:347px"><strong>TREVOR BUNGEY</strong> <span>(Director / Licensee):</span></h2>
      <div class="profile-photo" style="left:371px;top:411px;height:247px" role="img" aria-label="Headshot of Trevor Bungey in a navy suit and striped tie on a white background"></div>
      <div class="copy" style="top:371px">
        <span>Trevor has worked in various roles inclusive of being a Real Estate Agent, Bank</span>
        <span>Manager, Financial Counsellor, Mortgage Broker, &amp; previously</span>
        <span>a Commercial Pilot. He spent eight years in remote Western</span>
        <span>Australia, where he worked for an international mining</span>
        <span>company creating strategies to help support the well-being</span>
        <span>of employees. Trevor’s focus in life has always been to help</span>
        <span>people. To him, it is always about the relationship. Trevor gets</span>
        <span>enormous satisfaction from seeing individuals, families, and</span>
        <span>businesses thrive financially. He has become a skilled</span>
        <span>negotiator with extensive experience working for</span>
        <span>a number of corporations and private firms.</span>
      </div>
      <div class="copy" style="top:560px">
        <span>What differentiates Trevor is his compassion and</span>
        <span>commitment to people. He works hard to be</span>
        <span>an excellent communicator with the aim of</span>
        <span>achieving great results. He  has extensive sales</span>
        <span>experience with incredible ability to push the</span>
        <span>boundaries, think outside the box and</span>
        <span>meet or surpass expectations. This is</span>
        <span>why his clients keep coming back &amp;</span>
        <span>continue to refer well into the future.</span>
      </div>
      <div class="contact-bar" style="top:658px">
        <div class="contact-row" style="top:8px"><span class="phone">0400 362 917</span>
          <span class="icon-dot"><svg width="8" height="8" viewBox="0 0 8 8"><path d="M1.5 1 l1.4 -.2 l.8 1.7 l-.9 .7 q.8 1.7 2 2 l.7 -.9 l1.7 .8 l-.2 1.4 q-4.5 .3 -5.5 -5.5z" fill="#10223a"/></svg></span></div>
        <div class="contact-row" style="top:27px"><span class="email">trevor@pinecrestrealestate-example.com.au</span>
          <span class="icon-dot"><svg width="8" height="8" viewBox="0 0 8 8" fill="none" stroke="#10223a" stroke-width="1"><rect x=".8" y="1.8" width="6.4" height="4.6"/><path d="M.8 1.8 l3.2 2.5 l3.2 -2.5"/></svg></span></div>
      </div>
    </div>
  </section>

</div>
</body>
</html>
```